Presentation Folder, for Cancer Awareness, VERY COLORFULL AND MODERN

This will be a standard size folder that will hold standard 8 1/2 x 11 papers with a business card slot on the flap, this is a very easy project with very little text and the design for the back page is already done so all you really have to do is make a very nice colorful front cover, you will see my attachments are labeled and I gave you alot of instructions, this should be a very fast easy project
Updates

Reason: there has not been enough quality designs, sorry

Target Market(s)

Our Target Market is Dr's that Deal with Cancer patients

Industry/Entity Type

Healthcare

Font styles to use
Serif

Colors

Designer to choose colors to be used in the design.

Requirements
Must have
• Project must be tasteful and look professional with the ribbons as the main focal point in the center of folder the folder should be a nice gray color to accent the color of the ribbons , the back page needs no design it is the" Sorvane Test" in the attachments I sent
Nice to have
• I would like the ribbons displayed in a row, I included a logo sample layout
• a picture on the front of the folder under the words Hereditary Cancer Screening - Then under that put the words - The Power of Knowledge - then add the picture I labeled Great Picture in the attachments

```html
<!DOCTYPE html>
<html lang="en">
<head>
<meta charset="utf-8">
<title>Hereditary Cancer Screening Folder</title>
<link href="https://fonts.googleapis.com/css2?family=Lato:wght@400;700;900&family=Fira+Sans+Condensed:ital,wght@1,300&display=swap" rel="stylesheet">
<style>
:root{
  --red:#e8403a;
  --pink-title:#e8385f;
  --pink-soft:#f9dbe6;
  --blue-soft:#dceffa;
  --pink-list:#f07aa6;
  --stripe:#ececec;
  --ink:#222;
  --grey-text:#8a8a8a;
  --lynch:#fdc637;
  --peutz:#a8c23c;
  --lifr:#3daa4f;
  --cowden:#1aa0db;
  --gastric:#666;
  --page-right:#f4f4f5;
  --rb-breast:#f06fa0;
  --rb-ovarian:#1fa8a0;
  --rb-endometrial:#f5a25d;
  --rb-gastric:#8e96e0;
  --rb-colorectal:#1d3f8f;
  --rb-pancreatic:#7b3fa0;
  --rb-melanoma:#2a2a2a;
  --rb-prostate:#6cc3ea;
  --rb-lung:#c9c9c9;
  --rb-colon:#2f6fd0;
}
*{margin:0;padding:0;box-sizing:border-box}
html,body{width:1200px;height:800px;overflow:hidden;background:#fff}
body{font-family:"Lato",sans-serif;color:var(--ink);position:relative}
.page{position:absolute;top:0;height:800px;width:600px}
.page-back{left:0;background:#fff}
.page-front{left:600px;background:var(--page-right)}

.brand{position:absolute;left:32px;top:46px;font-size:19px;letter-spacing:6px;color:var(--red);font-weight:400}
.contact{position:absolute;left:32px;top:72px;font-size:6px;color:#555;line-height:9px;letter-spacing:.4px}
.menu-title{position:absolute;right:53px;top:44px;font-size:21px;font-weight:900;color:var(--red)}
.menu-title sup{font-size:8px}
.clia{position:absolute;right:53px;top:83px;font-size:6px;color:#555;letter-spacing:.4px}
.clia b{font-weight:700}

.gene-table{position:absolute;left:133px;top:110px;width:318px;border-collapse:collapse;font-size:7.6px}
.gene-table tr{height:15.83px}
.gene-table th{background:var(--red);color:#fff;font-weight:400;text-align:left;font-size:8.2px;letter-spacing:.3px;padding-left:6px}
.gene-table th.organ-head{padding-left:0}
.gene-table td{padding:0}
.gene-table td.gene{color:var(--red);font-weight:900;padding-left:6px;width:105px;letter-spacing:.4px}
.gene-table td.organ{font-weight:700;color:#333}
.gene-table tr.stripe td{background:var(--stripe)}
.gene-table tr.group td{color:#fff;font-weight:400;font-size:8.2px;letter-spacing:.4px;padding-left:14px}
.gene-table tr.sub td.gene{padding-left:15px}
.group.lynch td{background:var(--lynch)}
.group.peutz td{background:var(--peutz)}
.group.lifr td{background:var(--lifr)}
.group.cowden td{background:var(--cowden)}
.group.gastric td{background:var(--gastric)}

.web{position:absolute;left:165px;top:766px;font-size:11px;letter-spacing:7px;color:#555}

.banner{position:absolute;left:48px;top:53px;width:507px;height:53px}
.cover-title{position:absolute;left:0;width:600px;top:58px;text-align:center;font-size:35px;font-weight:900;color:var(--pink-title);letter-spacing:.5px}
.tagline{position:absolute;left:0;width:600px;top:127px;text-align:center;font-size:25.5px;font-weight:900;color:#111}
.family-photo{position:absolute;left:21px;top:175px;width:559px;height:372px;background:linear-gradient(160deg,#e9e6e0 0%,#c9b7a0 40%,#9a8a78 70%,#d8d3cb 100%)}
.cancer-list{position:absolute;left:0;width:600px;top:558px;text-align:center;font-family:"Fira Sans Condensed",sans-serif;font-style:italic;font-weight:300;font-size:24px;line-height:31px;color:var(--pink-list)}
.ribbon-row{position:absolute;left:125px;top:630px;width:350px;height:52px}
.ribbon-row path{fill:none;stroke-width:6;stroke-linecap:butt;stroke-linejoin:round}
.front-brand{position:absolute;left:35px;top:700px;width:130px;text-align:center}
.front-brand .mark{width:30px;height:30px;border-radius:50%;background:var(--red);margin:0 auto 10px}
.front-brand .name{font-size:13px;letter-spacing:4px;color:var(--red)}
.promise{position:absolute;right:60px;top:735px;font-size:20px;font-weight:900;color:var(--grey-text);letter-spacing:.5px}
</style>
</head>
<body>

<section class="page page-back">
  <div class="brand">GENAVERA</div>
  <div class="contact">820 MARLOWE AVENUE | SUITE 4 | BROOKFIELD, OH 44403<br>(tel) 555.210.4416 | (fax) 555.210.4417 | care@genavera.com</div>
  <div class="menu-title">SORVANE<sup>™</sup> Test Menu</div>
  <div class="clia">CLIA# 00X0000000 | <b>GENAVERA.COM</b></div>

  <table class="gene-table">
    <tr><th>GENE</th><th class="organ-head">CANCER-ASSOCIATED ORGAN/SYSTEMS</th></tr>
    <tr><td class="gene">APC</td><td class="organ">Colon</td></tr>
    <tr class="stripe"><td class="gene">ATM</td><td class="organ">Breast/Pancreatic/Brain</td></tr>
    <tr><td class="gene">BARD1</td><td class="organ">Breast/Ovarian</td></tr>
    <tr class="stripe"><td class="gene">BMPR1A</td><td class="organ">Colon</td></tr>
    <tr><td class="gene">BRCA1</td><td class="organ">Breast/Ovarian/Prostate</td></tr>
    <tr class="stripe"><td class="gene">BRCA2</td><td class="organ">Breast/Ovarian/Prostate</td></tr>
    <tr><td class="gene">BRIP1</td><td class="organ">Breast/Ovarian</td></tr>
    <tr class="stripe"><td class="gene">CDK4</td><td class="organ">Melanoma</td></tr>
    <tr><td class="gene">P16 (CDKN2A)</td><td class="organ">Melanoma/Breast/Pancreatic/Squamous</td></tr>
    <tr class="stripe"><td class="gene">FANCC</td><td class="organ">Blood</td></tr>
    <tr><td class="gene">MEN1</td><td class="organ">Thyroid/Parathyroid</td></tr>
    <tr class="stripe"><td class="gene">MET</td><td class="organ">Renal/Hepatic</td></tr>
    <tr><td class="gene">MRE11A</td><td class="organ">Ovarian/Breast</td></tr>
    <tr class="stripe"><td class="gene">NBN</td><td class="organ">Breast/Ovarian/Prostate/Melanoma</td></tr>
    <tr><td class="gene">NF1</td><td class="organ">Blood</td></tr>
    <tr class="stripe"><td class="gene">NTRK1</td><td class="organ">Thyroid/Parathyroid</td></tr>
    <tr><td class="gene">PALB2</td><td class="organ">Breast/Ovarian/Pancreatic</td></tr>
    <tr class="stripe"><td class="gene">PTCH1</td><td class="organ">Melanoma/Brain/Breast/Colon</td></tr>
    <tr><td class="gene">RAD50</td><td class="organ">Breast/Ovarian</td></tr>
    <tr class="stripe"><td class="gene">RAD51C</td><td class="organ">Ovarian/Breast</td></tr>
    <tr><td class="gene">RAD51D</td><td class="organ">Ovarian/Breast</td></tr>
    <tr class="stripe"><td class="gene">RET</td><td class="organ">Lung/Thyroid/Parathyroid</td></tr>
    <tr><td class="gene">SMAD4</td><td class="organ">Colon/Pancreas</td></tr>
    <tr class="group lynch"><td colspan="2">LYNCH SYNDROME GENES</td></tr>
    <tr class="sub"><td class="gene">MLH1</td><td class="organ">Colorectal/Ovarian</td></tr>
    <tr class="sub stripe"><td class="gene">MSH2</td><td class="organ">Colorectal/Ovarian</td></tr>
    <tr class="sub"><td class="gene">MSH6</td><td class="organ">Colorectal/Ovarian</td></tr>
    <tr class="sub stripe"><td class="gene">PMS2</td><td class="organ">Colorectal/Ovarian</td></tr>
    <tr class="sub"><td class="gene">EPCAM</td><td class="organ">Colorectal</td></tr>
    <tr class="group peutz"><td colspan="2">PEUTZ-JEGHERS SYNDROME GENE</td></tr>
    <tr class="sub"><td class="gene">STK11</td><td class="organ">Breast/Ovarian/Melanoma/Colorectal/Lung</td></tr>
    <tr class="group lifr"><td colspan="2">LI-FRAUMENI SYNDROME GENE</td></tr>
    <tr class="sub"><td class="gene">CHEK2</td><td class="organ">Breast/Ovarian/Prostate</td></tr>
    <tr class="sub stripe"><td class="gene">PT53</td><td class="organ">Breast/Bladder/Ovarian/Squamous</td></tr>
    <tr class="group cowden"><td colspan="2">COWDEN SYNDROME GENE</td></tr>
    <tr class="sub stripe"><td class="gene">PTEN</td><td class="organ">Endometrium/Breast/Prostate/Lung</td></tr>
    <tr class="group gastric"><td colspan="2">HEREDITARY DIFFUSE GASTRIC CANCER SYNDROME GENE</td></tr>
    <tr class="sub stripe"><td class="gene">CDH1</td><td class="organ">Breast/Gastric/Ovarian/Prostate</td></tr>
    <tr class="sub"><td class="gene">VHL</td><td class="organ">Renal</td></tr>
  </table>

  <div class="web">www.genavera.com</div>
</section>

<section class="page page-front">
  <svg class="banner" viewBox="0 0 507 53" aria-hidden="true">
    <polygon points="0,0 252,0 252,53 0,53 18,26.5" fill="var(--pink-soft)"/>
    <polygon points="252,0 507,0 489,26.5 507,53 252,53" fill="var(--blue-soft)"/>
  </svg>
  <h1 class="cover-title">Hereditary Cancer Screening</h1>
  <h2 class="tagline">The Power of Knowledge</h2>
  <div class="family-photo" role="img" aria-label="Photo of a multi-generation family sharing a meal at an outdoor wooden table"></div>
  <p class="cancer-list">Breast, Ovarian, Endometrial, Gastric, Colorectal,<br>Pancreatic, Melanoma, Prostate, lung, Colon</p>

  <svg class="ribbon-row" viewBox="0 0 350 52" role="img" aria-label="Row of awareness ribbons in the colours of the listed cancers">
    <defs>
      <path id="ribbon" d="M4 48 L13 28 C21 14 19 4 13 4 C7 4 5 14 13 28 L22 48"/>
    </defs>
    <use href="#ribbon" x="3" style="stroke:var(--rb-breast)"/>
    <use href="#ribbon" x="38" style="stroke:var(--rb-ovarian)"/>
    <use href="#ribbon" x="73" style="stroke:var(--rb-endometrial)"/>
    <use href="#ribbon" x="108" style="stroke:var(--rb-gastric)"/>
    <use href="#ribbon" x="143" style="stroke:var(--rb-colorectal)"/>
    <use href="#ribbon" x="178" style="stroke:var(--rb-pancreatic)"/>
    <use href="#ribbon" x="213" style="stroke:var(--rb-melanoma)"/>
    <use href="#ribbon" x="248" style="stroke:var(--rb-prostate)"/>
    <use href="#ribbon" x="283" style="stroke:var(--rb-lung)"/>
    <use href="#ribbon" x="318" style="stroke:var(--rb-colon)"/>
  </svg>

  <div class="front-brand"><div class="mark"></div><div class="name">GENAVERA</div></div>
  <div class="promise">Fast &nbsp;|&nbsp; Comprehensive &nbsp;|&nbsp; Easy</div>
</section>

</body>
</html>
```